Modern Verdell Tree Care Website

I need a website for a full service Tree Care company. The company provides tree pruning, tree removal, tree preservation, emergency services, stump grinding, and emergency tree services.

Target Market(s)

Customers that need tree services

Industry/Entity Type

Landscaping, Tree Services

Coding

Coded - Design and coding required

Number of Pages Required

5+ page

Font styles to use
Sans Serif

Requirements
Must have
• Good clean design that showcases the services the company provides.
Nice to have
• Services page; contact form, blog, home page, about page

```html
<!DOCTYPE html>
<html lang="en">
<head>
<meta charset="utf-8">
<title>Verdell Tree Care</title>
<link href="https://fonts.googleapis.com/css2?family=Bowlby+One&family=Kanit:wght@400;500;600&family=Inter:wght@400;500;600&display=swap" rel="stylesheet">
<style>
:root{
  --lime:#8cc63f;
  --green:#5a9a1e;
  --forest:#2f5e0f;
  --deep:#1b2f0f;
  --orange:#f7941d;
  --ink:#1d1d1d;
  --body:#444;
  --cream:#f6f5ee;
  --card:#f3f6f1;
  --white:#fff;
}
*{box-sizing:border-box;margin:0;padding:0}
html,body{width:1200px;height:3546px;overflow:hidden}
body{position:relative;background:var(--white);font-family:"Inter",sans-serif;color:var(--body)}
.abs{position:absolute}
h1,h2,h3,h4{font-family:"Kanit",sans-serif;font-weight:500;color:var(--ink)}
.eyebrow{font-family:"Kanit",sans-serif;font-size:19px;color:var(--lime);letter-spacing:.3px}
.btn{display:inline-flex;align-items:center;justify-content:center;font-family:"Kanit",sans-serif;font-size:14px;color:#fff;border-radius:4px}
.btn-orange{background:var(--orange)}
.btn-green{background:linear-gradient(90deg,var(--lime),var(--green))}

/* top bar */
.topbar{top:0;left:0;width:1200px;height:22px;background:var(--lime);color:#fff;font-size:11px;font-weight:500}
.topbar .l{left:190px;top:4px}
.topbar .r{right:190px;top:4px;display:flex;gap:26px}

/* hero */
.hero{top:22px;left:0;width:1200px;height:583px;background:linear-gradient(120deg,#c7661b 0%,#7a6b2a 22%,#4e6a1f 45%,#6f8a2b 70%,#3f5516 100%)}
.hero::after{content:"";position:absolute;inset:0;background:rgba(20,30,10,.35)}
.logo-box{top:38px;left:190px;width:178px;height:56px;background:#fff;border-radius:4px;z-index:2;display:flex;align-items:center;justify-content:center;gap:8px}
.brand{font-family:"Kanit",sans-serif;font-weight:600;color:var(--green);font-size:20px;letter-spacing:.5px}
.brand-dot{width:14px;height:14px;background:var(--orange)}
.nav{top:38px;left:380px;width:630px;height:56px;background:#fff;border-radius:4px;z-index:2;display:flex;align-items:center;padding-left:34px;font-size:12px;color:var(--ink)}
.nav span{padding:0 20px;border-right:1px solid #bbb;line-height:12px}
.nav span:nth-child(5){border:none}
.nav .btn{position:absolute;right:13px;top:12px;width:101px;height:32px;font-size:12px;font-family:"Inter",sans-serif}
.hero-copy{top:179px;left:0;width:1200px;text-align:center;z-index:2;color:#fff}
.pill{display:inline-block;background:var(--lime);font-size:11px;font-weight:500;padding:7px 22px;border-radius:3px}
.hero-title{font-family:"Bowlby One",sans-serif;font-weight:400;color:#fff;font-size:45px;line-height:48px;margin-top:16px;letter-spacing:.5px;text-shadow:0 2px 8px rgba(0,0,0,.25)}
.hero-sub{font-size:16px;margin-top:18px;font-weight:400;color:#fff}
.hero-copy .btn{width:122px;height:38px;margin-top:18px;font-size:14px}

/* contact strip */
.strip{top:534px;left:190px;width:819px;height:110px;background:#fff;border-radius:8px;box-shadow:0 6px 22px rgba(0,0,0,.08);z-index:3}
.phone{top:38px;display:flex;gap:10px;align-items:center}
.ph-ico{width:46px;height:36px}
.ph-num{font-family:"Kanit",sans-serif;font-size:16px;color:var(--ink);line-height:18px}
.ph-lab{font-size:12px;color:#999}
.call{left:467px;top:36px;font-family:"Kanit",sans-serif;font-size:16px;color:var(--ink);line-height:20px}
.call b{color:var(--lime);font-weight:500}
.strip .btn{left:676px;top:36px;width:122px;height:40px}

/* about */
.about-text{top:728px;left:190px;width:385px}
.about-text h2{font-size:35px;line-height:40px;margin-top:4px}
.about-text p{font-size:12px;line-height:20px;margin-top:16px}
.about-text .btn{width:119px;height:38px;margin-top:26px;font-size:13px}
.about-img{top:707px;left:638px;width:371px;height:361px;border-radius:26px;background:linear-gradient(150deg,#3e6b22,#8f9b62 45%,#d9d6c7 60%,#4f6f2d)}

/* services */
.services-band{top:1131px;left:0;width:1200px;height:321px;background:linear-gradient(110deg,#1f3f10,#2f6314 45%,#265512 75%,#1a3a0c)}
.services-head{top:1190px;left:0;width:1200px;text-align:center}
.services-head h2{color:#fff;font-size:35px;line-height:40px;margin-top:4px}
.svc{top:1339px;width:120px;height:202px;background:var(--card);border-radius:6px;text-align:center}
.svc .ic{width:72px;height:72px;border-radius:50%;background:#fff;margin:40px auto 16px;display:flex;align-items:center;justify-content:center}
.svc h4{font-size:16px;line-height:17px}
.svc.active{background:linear-gradient(180deg,var(--green),var(--lime))}
.svc.active h4{color:#fff}

/* why */
.why-img{top:1607px;left:190px;width:356px;height:388px;border-radius:0 40px 40px 0;background:var(--green)}
.why-img div{position:absolute;top:0;left:0;width:343px;height:378px;border-radius:0 34px 34px 0;background:linear-gradient(160deg,#9aa57a,#5f7b3a 40%,#b46a2d 60%,#46612a)}
.why-text{top:1655px;left:594px;width:420px}
.why-text h2{font-size:35px;line-height:40px;margin-top:4px}
.why-text p{font-size:12px;line-height:20px;margin-top:12px;width:410px}
.ticks{display:grid;grid-template-columns:201px 219px;row-gap:16px;margin-top:28px;font-size:12px;font-weight:500;color:var(--ink);white-space:nowrap}
.ticks div{display:flex;gap:10px;align-items:center}

/* portfolio */
.portfolio{top:2057px;left:0;width:1200px;height:537px;background:var(--forest)}
.port-head{top:2117px;left:190px}
.port-head .eyebrow{color:#fff}
.port-head h2{color:#fff;font-size:35px;line-height:40px;margin-top:2px}
.portfolio-btn{top:2131px;left:880px;width:129px;height:43px;font-size:14px}
.shot{border-radius:10px}

/* testimonials */
.testi-bg{top:2594px;left:0;width:1200px;height:566px;background:var(--cream)}
.testi-head{top:2657px;left:0;width:1200px;text-align:center}
.testi-head h2{font-size:35px;line-height:41px;margin-top:4px}
.quote{top:2782px;width:399px;height:238px;background:#fff;padding:30px 32px}
.quote p{font-size:11px;line-height:19px;color:var(--body);margin-top:14px}
.who{display:flex;gap:14px;align-items:center;margin-top:22px}
.avatar{width:48px;height:48px;border-radius:50%;background:linear-gradient(#6a7b8a,#2c3440)}
.who b{display:block;font-size:12px;color:var(--ink);font-weight:600}
.who span{font-size:11px;color:#999}
.dots{top:3044px;left:562px;display:flex;gap:11px;align-items:center}
.dots i{width:6px;height:6px;border-radius:50%;background:#ccc;display:block}
.dots i.on{width:10px;height:10px;background:var(--lime)}

/* footer */
.footer{top:3160px;left:0;width:1200px;height:386px;background:var(--deep)}
.cta{top:3117px;left:190px;width:819px;height:108px;border-radius:10px;background:linear-gradient(90deg,var(--green),var(--lime));z-index:3}
.cta h3{position:absolute;left:47px;top:25px;color:#fff;font-size:24px;line-height:29px}
.cta .g{position:absolute;top:33px;width:128px;height:42px;border:2px solid #fff;font-family:"Kanit",sans-serif;font-size:14px;border-radius:3px;display:flex;align-items:center;justify-content:center}
.foot-logo{top:3270px;left:237px;display:flex;gap:10px;align-items:center}
.foot-logo .brand{color:#fff;font-size:26px}
.fcol{top:3272px;color:#fff}
.fcol h4{color:#fff;font-size:14px;font-weight:500;padding-bottom:6px;position:relative}
.fcol h4::after{content:"";position:absolute;left:0;bottom:0;width:36px;height:2px;background:var(--lime)}
.fcol ul{list-style:none;margin-top:20px;font-size:11px;line-height:25px;color:#d7dccf}
.fphone{display:flex;gap:10px;align-items:center;margin-top:20px}
.fphone b{display:block;font-size:14px;font-weight:500;color:#fff}
.fphone span{font-size:11px;color:#8a967f}
.copy{top:3524px;left:0;width:1200px;text-align:center;font-size:9px;color:#b8c0ae}
</style>
</head>
<body>

<div class="abs topbar">
  <span class="abs l">Call Verdell for All Your Tree Care Needs</span>
  <span class="abs r"><span>(555) 214-3870</span><span>(555) 306-7182</span></span>
</div>

<div class="abs hero" role="img" aria-label="Arborist in orange safety vest trimming a hedge with pruning shears"></div>

<div class="abs logo-box"><span class="brand-dot"></span><span class="brand">VERDELL</span></div>
<nav class="abs nav">
  <span>Home</span><span>About Us</span><span>Services</span><span>Portfolio</span><span>Testimonials</span>
  <a class="btn btn-orange">Contact Us</a>
</nav>

<div class="abs hero-copy">
  <span class="pill">WELCOME TO VERDELL TREE CARE</span>
  <h1 class="hero-title">TRANSFORMING LANDSCAPES<br>ONE TREE AT A TIME</h1>
  <p class="hero-sub">Your Trusted Partner for Expert Tree Care Services</p>
  <a class="btn btn-orange">Get Started</a>
</div>

<div class="abs strip">
  <div class="abs phone" style="left:22px">
    <svg class="ph-ico" viewBox="0 0 46 36"><circle cx="16" cy="18" r="16" fill="#e3f0d3"/><path d="M22 9c-2 0-3 1-3 3 0 8 6 15 14 15 2 0 3-1 3-3l-4-3-3 2c-3-1-6-4-7-7l2-3z" fill="none" stroke="#8cc63f" stroke-width="1.6"/><path d="M30 9a7 7 0 0 1 6 6M29 13a3 3 0 0 1 3 3" fill="none" stroke="#8cc63f" stroke-width="1.4"/></svg>
    <div><div class="ph-num">(555) 214-3870</div><div class="ph-lab">Phone</div></div>
  </div>
  <div class="abs phone" style="left:244px">
    <svg class="ph-ico" viewBox="0 0 46 36"><circle cx="16" cy="18" r="16" fill="#e3f0d3"/><path d="M22 9c-2 0-3 1-3 3 0 8 6 15 14 15 2 0 3-1 3-3l-4-3-3 2c-3-1-6-4-7-7l2-3z" fill="none" stroke="#8cc63f" stroke-width="1.6"/><path d="M30 9a7 7 0 0 1 6 6M29 13a3 3 0 0 1 3 3" fill="none" stroke="#8cc63f" stroke-width="1.4"/></svg>
    <div><div class="ph-num">(555) 306-7182</div><div class="ph-lab">Phone</div></div>
  </div>
  <div class="abs call">Call <b>HOLLOWAY</b> for a<br>Free Estimate</div>
  <a class="abs btn btn-green">Get A Quote</a>
</div>

<section class="abs about-text">
  <div class="eyebrow">ABOUT US</div>
  <h2>Who We Are</h2>
  <p>At Verdell Tree Care, we are more than just a tree service company, we are stewards of our beautiful trees. With a passion deeply rooted in arboriculture, we embark on a mission to promote the health, beauty, and safety of your trees and landscapes.</p>
  <p>Whether it's expert tree trimming to enhance aesthetics, meticulous tree removal to mitigate hazards, or comprehensive tree health assessments to ensure safety, we approach each task with unwavering dedication and attention to detail.</p>
  <a class="btn btn-green">Learn More</a>
</section>
<div class="abs about-img" role="img" aria-label="Arborist in a bucket lift cutting a tree trunk with a chainsaw"></div>

<div class="abs services-band" role="img" aria-label="Tree care machinery working in a green field"></div>
<div class="abs services-head">
  <div class="eyebrow">OUR SERVICES</div>
  <h2>Explore Our Comprehensive<br>Tree Care Solutions</h2>
</div>
<div class="abs svc" style="left:190px"><div class="ic"><svg width="40" height="40" viewBox="0 0 40 40" fill="none" stroke="#8cc63f" stroke-width="1.6"><circle cx="24" cy="13" r="8"/><path d="M24 21v14M8 35h28M12 20l4 4"/></svg></div><h4>Tree<br>Pruning</h4></div>
<div class="abs svc" style="left:330px"><div class="ic"><svg width="40" height="40" viewBox="0 0 40 40" fill="none" stroke="#8cc63f" stroke-width="1.6"><rect x="6" y="22" width="28" height="9" rx="4"/><circle cx="12" cy="26.5" r="2"/><path d="M16 14h10M21 10v4"/></svg></div><h4>Tree<br>Removal</h4></div>
<div class="abs svc active" style="left:470px"><div class="ic"><svg width="40" height="40" viewBox="0 0 40 40" fill="none" stroke="#5a9a1e" stroke-width="1.6"><circle cx="20" cy="13" r="8"/><path d="M20 21v8M6 28c6 0 9 4 14 4s8-2 14-6"/></svg></div><h4>Tree<br>Preservation</h4></div>
<div class="abs svc" style="left:610px"><div class="ic"><svg width="40" height="40" viewBox="0 0 40 40" fill="none" stroke="#8cc63f" stroke-width="1.6"><path d="M20 5l-7 10h4l-6 9h5l-6 8h20l-6-8h5l-6-9h4zM20 32v4"/></svg></div><h4>Emergency<br>Services</h4></div>
<div class="abs svc" style="left:750px"><div class="ic"><svg width="40" height="40" viewBox="0 0 40 40" fill="none" stroke="#8cc63f" stroke-width="1.6"><rect x="8" y="20" width="24" height="10" rx="2"/><circle cx="14" cy="32" r="3"/><circle cx="27" cy="32" r="3"/><path d="M14 20l6-10 6 4"/></svg></div><h4>Stump<br>Grinding</h4></div>
<div class="abs svc" style="left:890px"><div class="ic"><svg width="40" height="40" viewBox="0 0 40 40" fill="none" stroke="#8cc63f" stroke-width="1.6"><path d="M13 8l-5 8h3l-4 7h12l-4-7h3zM27 10l-4 7h3l-4 6h10l-4-6h3zM13 23v9M27 23v9M5 32h30"/></svg></div><h4>Storm Damage<br>Cleanup</h4></div>

<div class="abs why-img"><div role="img" aria-label="Climber with helmet and chainsaw cutting branches up in a tree"></div></div>
<section class="abs why-text">
  <div class="eyebrow" style="color:var(--green)">VERDELL TREE CARE</div>
  <h2>Why Choose Us?</h2>
  <p>From our unwavering commitment to excellence to our dedication to preserving the natural beauty of your landscape, discover why Verdell Tree Care stands out as the premier choice for all your tree care needs.</p>
  <div class="ticks">
    <div><svg width="18" height="16" viewBox="0 0 18 16"><path d="M1 8l5 5L17 2" fill="none" stroke="#5a9a1e" stroke-width="3"/></svg>Licensed and Insured</div>
    <div><svg width="18" height="16" viewBox="0 0 18 16"><path d="M1 8l5 5L17 2" fill="none" stroke="#5a9a1e" stroke-width="3"/></svg>24-Hours Emergency Services</div>
    <div><svg width="18" height="16" viewBox="0 0 18 16"><path d="M1 8l5 5L17 2" fill="none" stroke="#5a9a1e" stroke-width="3"/></svg>Professional Work</div>
    <div><svg width="18" height="16" viewBox="0 0 18 16"><path d="M1 8l5 5L17 2" fill="none" stroke="#5a9a1e" stroke-width="3"/></svg>Locally Owned &amp; Operated</div>
    <div><svg width="18" height="16" viewBox="0 0 18 16"><path d="M1 8l5 5L17 2" fill="none" stroke="#5a9a1e" stroke-width="3"/></svg>Free Estimates</div>
    <div><svg width="18" height="16" viewBox="0 0 18 16"><path d="M1 8l5 5L17 2" fill="none" stroke="#5a9a1e" stroke-width="3"/></svg>Safety is Our No.1 Priority</div>
    <div><svg width="18" height="16" viewBox="0 0 18 16"><path d="M1 8l5 5L17 2" fill="none" stroke="#5a9a1e" stroke-width="3"/></svg>Licensed Arborist on Staff</div>
  </div>
</section>

<div class="abs portfolio"></div>
<div class="abs port-head">
  <div class="eyebrow">OUR PORTFOLIO</div>
  <h2>Worked We Have Done</h2>
</div>
<a class="abs btn btn-orange portfolio-btn">More Portfolio</a>
<div class="abs shot" style="top:2213px;left:190px;width:404px;height:151px;background:linear-gradient(100deg,#2f6b1c,#5e9a2c 50%,#c98e7a)" role="img" aria-label="Hedge shears trimming a green hedge"></div>
<div class="abs shot" style="top:2213px;left:607px;width:194px;height:151px;background:linear-gradient(140deg,#6b5a48,#b8a58a 55%,#d0762e)" role="img" aria-label="Chainsaw cutting through a log"></div>
<div class="abs shot" style="top:2213px;left:815px;width:194px;height:151px;background:linear-gradient(180deg,#3f6ab5,#5d8a3a 55%,#6f9a3a)" role="img" aria-label="Crane truck removing a tree in a yard"></div>
<div class="abs shot" style="top:2378px;left:190px;width:194px;height:152px;background:linear-gradient(120deg,#8a6b4a,#c7a27a 45%,#3c5f9a)" role="img" aria-label="Worker sawing into a pine trunk"></div>
<div class="abs shot" style="top:2378px;left:398px;width:194px;height:152px;background:linear-gradient(180deg,#a9b3b8,#7a6e5e 60%,#5b5a56)" role="img" aria-label="Felled tree lying across a street"></div>
<div class="abs shot" style="top:2378px;left:604px;width:405px;height:152px;background:linear-gradient(100deg,#5b4a32,#c08a2e 45%,#d9c7a7 75%,#7a6648)" role="img" aria-label="Stump grinder throwing wood chips"></div>

<div class="abs testi-bg"></div>
<div class="abs testi-head">
  <div class="eyebrow">CLIENT TESTIMONIALS</div>
  <h2>See What Our Clients<br>Have to Say:</h2>
</div>
<article class="abs quote" style="left:190px">
  <svg width="18" height="12" viewBox="0 0 18 12"><path d="M0 12V6l3-6h3L4 6h3v6zM10 12V6l3-6h3l-2 6h3v6z" fill="#8cc63f"/></svg>
  <p>I Was Amazed By The Professionalism And Efficiency Of The Verdell Tree Care Team. They Took Care Of A Hazardous Tree On My Property With Precision And Care. I Highly Recommend Their Services To Anyone In Need Of Expert Tree Care.</p>
  <div class="who"><div class="avatar" role="img" aria-label="Client portrait"></div><div><b>Dana Whitfield</b><span>Homeowner</span></div></div>
</article>
<article class="abs quote" style="left:610px">
  <svg width="18" height="12" viewBox="0 0 18 12"><path d="M0 12V6l3-6h3L4 6h3v6zM10 12V6l3-6h3l-2 6h3v6z" fill="#8cc63f"/></svg>
  <p>Choosing Verdell Tree Care Was The Best Decision I Made For My Property. Their Team Was Professional, Courteous, And Incredibly Skilled. They Transformed My Overgrown Trees Into A Beautifully Manicured Landscape. I Couldn't Be Happier With The Results.</p>
  <div class="who"><div class="avatar" role="img" aria-label="Client portrait"></div><div><b>Marcus Ellery</b><span>Homeowner</span></div></div>
</article>
<div class="abs dots"><i></i><i></i><i class="on"></i><i></i><i></i></div>

<div class="abs footer"></div>
<div class="abs cta">
  <h3>Ready to Get Free Consultations<br>Any Kind Of It Solutions?</h3>
  <a class="g" style="left:500px;background:#fff;color:var(--green)">Get A Quote</a>
  <a class="g" style="left:640px;color:#fff">Learn More</a>
</div>

<div class="abs foot-logo"><span class="brand-dot" style="width:18px;height:18px"></span><span class="brand">VERDELL</span></div>
<div class="abs fcol" style="left:472px">
  <h4>Quick Links</h4>
  <ul><li>Home</li><li>About Us</li><li>Services</li><li>Portfolio</li><li>Testimonials</li><li>Contact Us</li></ul>
</div>
<div class="abs fcol" style="left:618px">
  <h4>Services</h4>
  <ul><li>Tree Pruning</li><li>Tree Removal</li><li>Tree Preservation</li><li>Emergency Services</li><li>Stump Grinding</li><li>Emergency Tree Services</li></ul>
</div>
<div class="abs fcol" style="left:808px">
  <h4>Contact Info</h4>
  <div class="fphone" style="margin-left:12px"><svg width="30" height="30" viewBox="0 0 30 30" fill="none" stroke="#8cc63f" stroke-width="1.5"><path d="M10 4c-2 0-4 2-4 4 0 10 8 18 18 18 2 0 4-2 4-4l-5-4-3 3c-4-1-8-5-9-9l3-3z"/><path d="M19 4a8 8 0 0 1 7 7M18 9a3 3 0 0 1 3 3"/></svg><div><b>(555) 214-3870</b><span>Phone</span></div></div>
  <div class="fphone" style="margin-left:12px;margin-top:26px"><svg width="30" height="30" viewBox="0 0 30 30" fill="none" stroke="#8cc63f" stroke-width="1.5"><path d="M10 4c-2 0-4 2-4 4 0 10 8 18 18 18 2 0 4-2 4-4l-5-4-3 3c-4-1-8-5-9-9l3-3z"/><path d="M19 4a8 8 0 0 1 7 7M18 9a3 3 0 0 1 3 3"/></svg><div><b>(555) 306-7182</b><span>Phone</span></div></div>
</div>
<div class="abs copy">© 2024 Verdell Tree Care. All Rights Reserved.</div>

</body>
</html>
```